Clean Modern Skin Product branding/ label.

I need a label for a skincare line. The company is Dermaloft but product names will vary. A couple products to list are:
Sensitive Cleanser, Lumeno, Repair, Halo up, Mendora, Mendora Plus, Mendora Intense, Tavelo, Balance and Vivanto.

I would like the color scheme to be muted greens, grays, tourquise. The bottles are white, boston shaped with pumps, and ounces are 2, 4, 8, 16 ounces. When I choose the design, I can give you exact label sizes. Along with the ingredience already on the product label.

The look I desire is clean, minimal. A modern, organic look. Ideas that come to mind are a Veloraine,https://www.veloraine-example.com/product/2846/37204/3-step/step-2-exfoliate/clarifying-lotion-1 and the simplicity of Bo Tarn.

Both styles high light the name, in this case Dermaloft, and then the specific product.

My product is clean utilizing pure ingredients rather that a bunch fillers and binders. When I work with my clients I normally will say we need to "restore the balance" from over use of harsh products. That is why this lines works. It restores the skin to it's natural state. The process is simple, so I would like the label to reflect that simplicity.

Target Market(s)

Anyone with sensitive skin. So gender neutral

Industry/Entity Type

Skin Care Product

Font styles to use
Serif
Sans Serif
Decorative

Colors
acd037
33b8a4
fcfefd
85cae6
d3d3d3

Requirements
Must have
• Logo, name of product and color identity for cleanser, Active products, moisturizers
• I am thinking we could have one color for a cleanser and a space where I can put a sticker on which cleanser it is. Acne Cleasner, Sensitive Cleanser, and Cleanser.
Nice to have
• Not sure....suprise me. I would like the font to stay the same on the DERMALOFT, but you can change color, or color of leaf.
Should not have
• Too busy, too crowded or look like every other skincare line

```html
<!DOCTYPE html>
<html lang="en">
<head>
<meta charset="utf-8">
<title>Dermaloft Label Range</title>
<link rel="stylesheet" href="https://fonts.googleapis.com/css2?family=Marcellus&family=Josefin+Sans:wght@400&display=swap">
<style>
  :root {
    --canvas: #ffffff;
    --lumeno-bg: #f3f2ed;
    --haloup-bg: #dcd8d1;
    --tavelo-bg: #dcdac8;
    --repair-bg: #cdc9b0;
    --cleanser-bg: #b3b19a;
    --vivanto-bg: #aaa9a2;
    --balance-bg: #52514c;
    --mendora-bg: #6b6a5e;
    --mendora-plus-bg: #4f4d45;
    --mendora-intense-bg: #3b3a34;
    --ink-dark: #7d7a68;
    --ink-light: #f4f2ea;
    --ink-muted: #cfccbd;
  }
  * { margin: 0; padding: 0; box-sizing: border-box; }
  html, body { width: 1200px; height: 806px; overflow: hidden; background: var(--canvas); }
  .range { position: relative; width: 1200px; height: 806px; }
  .label {
    position: absolute; width: 162px; height: 372px;
    background: var(--bg); color: var(--ink);
    font-family: "Josefin Sans", sans-serif; overflow: hidden;
  }
  .sprig { position: absolute; opacity: .35; }
  .sprig-top { top: -4px; right: -6px; width: 52px; height: 120px;
    background: radial-gradient(ellipse at 60% 40%, var(--ink) 0%, transparent 70%); }
  .sprig-bottom { top: 200px; left: -14px; width: 80px; height: 140px;
    background: radial-gradient(ellipse at 50% 40%, var(--ink) 0%, transparent 70%); opacity: .22; }
  .intro, .details {
    position: absolute; left: 0; right: 0; text-align: center;
    font-size: 6px; line-height: 8.5px; letter-spacing: .2px;
  }
  .intro { top: 53px; }
  .details { top: 276px; }
  .product-name {
    position: absolute; left: 0; right: 0; top: 147px; text-align: center;
    font-family: "Marcellus", serif; font-size: 20px; letter-spacing: 1.6px;
    line-height: 25px; color: var(--title);
  }
  .product-name.two-line { top: 125px; }
  .rule { position: absolute; top: 186px; left: 70px; width: 22px; height: 1px; background: var(--ink); opacity: .4; }
  .brand {
    position: absolute; left: 0; right: 0; top: 336px; text-align: center;
    font-family: "Marcellus", serif; font-size: 12px; letter-spacing: .3px; color: var(--ink);
  }
  .light { --ink: var(--ink-dark); }
  .dark { --ink: var(--ink-muted); }
</style>
</head>
<body>
<main class="range">
  <section class="label light" style="left:28px;top:15px;--bg:var(--lumeno-bg);--title:#8f8a74">
    <div class="sprig sprig-top" role="img" aria-label="Line drawing of a leafy sprig"></div>
    <div class="sprig sprig-bottom" role="img" aria-label="Line drawing of a leafy sprig"></div>
    <p class="intro">text text text text<br>text text</p>
    <h2 class="product-name">Lumeno</h2><div class="rule"></div>
    <p class="details">text text text text<br>text text text text<br>text text text</p>
    <p class="brand">dermaloft</p>
  </section>
  <section class="label light" style="left:230px;top:15px;--bg:var(--haloup-bg);--title:#f6f3ec">
    <div class="sprig sprig-top" role="img" aria-label="Line drawing of a leafy sprig"></div>
    <div class="sprig sprig-bottom" role="img" aria-label="Line drawing of a leafy sprig"></div>
    <p class="intro">text text text text<br>text text</p>
    <h2 class="product-name">Halo Up</h2><div class="rule"></div>
    <p class="details">text text text text<br>text text text text<br>text text text</p>
    <p class="brand">dermaloft</p>
  </section>
  <section class="label light" style="left:428px;top:15px;--bg:var(--tavelo-bg);--title:#8a8772">
    <div class="sprig sprig-top" role="img" aria-label="Line drawing of a leafy sprig"></div>
    <div class="sprig sprig-bottom" role="img" aria-label="Line drawing of a leafy sprig"></div>
    <p class="intro">text text text text<br>text text</p>
    <h2 class="product-name">Tavelo</h2><div class="rule"></div>
    <p class="details">text text text text<br>text text text text<br>text text text</p>
    <p class="brand">dermaloft</p>
  </section>
  <section class="label light" style="left:633px;top:14px;--bg:var(--repair-bg);--title:#8c8a72">
    <div class="sprig sprig-top" role="img" aria-label="Line drawing of a leafy sprig"></div>
    <div class="sprig sprig-bottom" role="img" aria-label="Line drawing of a leafy sprig"></div>
    <p class="intro">text text text text<br>text text</p>
    <h2 class="product-name">Repair</h2><div class="rule"></div>
    <p class="details">text text text text<br>text text text text<br>text text text</p>
    <p class="brand">dermaloft</p>
  </section>

  <section class="label light" style="left:27px;top:426px;--bg:var(--cleanser-bg);--ink:#f1efe6;--title:#f7f5ee">
    <div class="sprig sprig-top" role="img" aria-label="Line drawing of a leafy sprig"></div>
    <div class="sprig sprig-bottom" role="img" aria-label="Line drawing of a leafy sprig"></div>
    <p class="intro">text text text text<br>text text</p>
    <h2 class="product-name two-line">Sensitive<br>Cleanser</h2><div class="rule"></div>
    <p class="details">text text text text<br>text text text text<br>text text text</p>
    <p class="brand">dermaloft</p>
  </section>
  <section class="label light" style="left:226px;top:426px;--bg:var(--vivanto-bg);--ink:#8e8d84;--title:#f7f5ee">
    <div class="sprig sprig-top" role="img" aria-label="Line drawing of a leafy sprig"></div>
    <div class="sprig sprig-bottom" role="img" aria-label="Line drawing of a leafy sprig"></div>
    <p class="intro">text text text text<br>text text</p>
    <h2 class="product-name">Vivanto</h2><div class="rule"></div>
    <p class="details">text text text text<br>text text text text<br>text text text</p>
    <p class="brand">dermaloft</p>
  </section>
  <section class="label dark" style="left:428px;top:426px;--bg:var(--balance-bg);--title:#f4f2ea">
    <div class="sprig sprig-top" role="img" aria-label="Line drawing of a leafy sprig"></div>
    <div class="sprig sprig-bottom" role="img" aria-label="Line drawing of a leafy sprig"></div>
    <p class="intro">text text text text<br>text text</p>
    <h2 class="product-name">Balance</h2><div class="rule"></div>
    <p class="details">text text text text<br>text text text text<br>text text text</p>
    <p class="brand">dermaloft</p>
  </section>
  <section class="label dark" style="left:629px;top:421px;--bg:var(--mendora-bg);--title:#f4f2ea">
    <div class="sprig sprig-top" role="img" aria-label="Line drawing of a leafy sprig"></div>
    <div class="sprig sprig-bottom" role="img" aria-label="Line drawing of a leafy sprig"></div>
    <p class="intro">text text text text<br>text text</p>
    <h2 class="product-name">Mendora</h2><div class="rule"></div>
    <p class="details">text text text text<br>text text text text<br>text text text</p>
    <p class="brand">dermaloft</p>
  </section>
  <section class="label dark" style="left:831px;top:421px;--bg:var(--mendora-plus-bg);--title:#f4f2ea">
    <div class="sprig sprig-top" role="img" aria-label="Line drawing of a leafy sprig"></div>
    <div class="sprig sprig-bottom" role="img" aria-label="Line drawing of a leafy sprig"></div>
    <p class="intro">text text text text<br>text text</p>
    <h2 class="product-name two-line">Mendora<br>Plus</h2><div class="rule"></div>
    <p class="details">text text text text<br>text text text text<br>text text text</p>
    <p class="brand">dermaloft</p>
  </section>
  <section class="label dark" style="left:1033px;top:426px;--bg:var(--mendora-intense-bg);--title:#f4f2ea">
    <div class="sprig sprig-top" role="img" aria-label="Line drawing of a leafy sprig"></div>
    <div class="sprig sprig-bottom" role="img" aria-label="Line drawing of a leafy sprig"></div>
    <p class="intro">text text text text<br>text text</p>
    <h2 class="product-name two-line">Mendora<br>Intense</h2><div class="rule"></div>
    <p class="details">text text text text<br>text text text text<br>text text text</p>
    <p class="brand">dermaloft</p>
  </section>
</main>
</body>
</html>
```